Visitenkarten-Design für das Business mit Gesundheit& Beauty
Zielgruppe
Ich bin selbständige Vertriebspartnerin von Vk. Die Visitenkarten sollen nicht zu verspielt wirken, eher geschäftlich. Dennoch könnte eine Verbindung zu den Bereichen Gesundheit & Beuuty dazukommen .
Hauptproduktmerkmal ist zum Beispiel die Aloe Vera, Naturprodukte.. mehr Infos auf : www.bettina-kolmar-beispiel.de
Instagram :bettikolmar
Eventuell könnte mein Slogan mit 'just more' noch einfließen, muss aber nicht. Bin für Ideen offen...
Aufgabenstellung
elegant und zeitlos, aber weich
Vielleicht eine goldene Aloe Vera irgendwie mit drauf?
Habe bei den dateien mal ein paar Screenshots hinzugefügt was ich recht schön fand

```html
<!DOCTYPE html>
<html lang="de">
<head>
<meta charset="utf-8">
<title>Bettina Kolmar – Visitenkarte</title>
<link rel="stylesheet" href="https://fonts.googleapis.com/css2?family=Lato:wght@300;400&display=swap">
<style>
  :root {
    --page-bg: #e9e6e1;
    --card-white: #ffffff;
    --ink: #2b2b2b;
    --ink-soft: #555555;
    --gold: #b8966a;
    --gold-line: #cdb08a;
    --beige-light: #ddd1bd;
    --beige-dark: #c4b498;
    --sage: #a8ab8f;
  }
  * { margin: 0; padding: 0; box-sizing: border-box; }
  html, body { width: 1200px; height: 900px; overflow: hidden; }
  body {
    background: var(--page-bg);
    display: flex;
    align-items: center;
    justify-content: center;
    gap: 40px;
    font-family: "Lato", sans-serif;
    color: var(--ink);
  }
  .card {
    position: relative;
    width: 560px;
    height: 362px;
    border-radius: 4px;
    box-shadow: 0 10px 30px rgba(0,0,0,0.15);
    overflow: hidden;
  }
  .card-front { background: var(--card-white); }

  .brand {
    position: absolute;
    left: 40px;
    top: 64px;
  }
  .brand-name {
    font-family: "Lato", sans-serif;
    font-weight: 400;
    font-size: 26px;
    color: var(--ink);
    white-space: nowrap;
  }
  .brand-tagline {
    margin-top: 6px;
    font-size: 11px;
    letter-spacing: 1px;
    color: var(--gold);
  }

  .addresses {
    position: absolute;
    right: 40px;
    top: 64px;
    text-align: right;
    font-size: 13px;
    line-height: 1.35;
    color: var(--ink-soft);
  }
  .address + .address { margin-top: 16px; }

  .divider {
    position: absolute;
    left: 40px;
    right: 40px;
    top: 190px;
    height: 1px;
    background: var(--gold-line);
  }

  .contacts {
    position: absolute;
    left: 40px;
    bottom: 40px;
    list-style: none;
    font-size: 13px;
    color: var(--ink-soft);
  }
  .contacts li {
    display: flex;
    align-items: center;
    gap: 10px;
    line-height: 1.5;
  }
  .contact-icon { width: 12px; height: 12px; flex: none; }

  .card-back { background: var(--beige-light); }
  .back-pattern {
    position: absolute;
    inset: 0;
    background:
      radial-gradient(ellipse at 20% 25%, rgba(168,171,143,0.35), transparent 55%),
      radial-gradient(ellipse at 80% 80%, rgba(168,171,143,0.3), transparent 55%),
      linear-gradient(135deg, var(--beige-light), var(--beige-dark));
  }
  .back-brand {
    position: absolute;
    inset: 0;
    display: flex;
    flex-direction: column;
    align-items: center;
    justify-content: center;
  }
  .back-brand .brand-name { font-size: 30px; }
  .back-brand .brand-tagline { margin-top: 8px; font-size: 12px; color: var(--ink-soft); }
</style>
</head>
<body>

  <section class="card card-front" aria-label="Vorderseite">
    <div class="brand">
      <div class="brand-name">Bettina Kolmar</div>
      <div class="brand-tagline">Natur, Pflege &amp; Stil</div>
    </div>

    <div class="addresses">
      <p class="address">Chemin des Tilleuls 12<br>8340 Bergwil</p>
      <p class="address">Rue des Lilas 7<br>6210 Lindenau</p>
    </div>

    <div class="divider"></div>

    <ul class="contacts">
      <li>
        <svg class="contact-icon" viewBox="0 0 24 24" aria-hidden="true"><path fill="var(--gold)" d="M6.6 10.8a15.1 15.1 0 0 0 6.6 6.6l2.2-2.2a1 1 0 0 1 1-.25 11.4 11.4 0 0 0 3.6.57 1 1 0 0 1 1 1V20a1 1 0 0 1-1 1A17 17 0 0 1 3 4a1 1 0 0 1 1-1h3.5a1 1 0 0 1 1 1c0 1.25.2 2.45.57 3.57a1 1 0 0 1-.25 1z"/></svg>
        044 000 12 34
      </li>
      <li>
        <svg class="contact-icon" viewBox="0 0 24 24" aria-hidden="true"><rect x="2" y="5" width="20" height="14" rx="2" fill="var(--gold)"/><path d="M3 6l9 7 9-7" fill="none" stroke="#fff" stroke-width="1.8"/></svg>
        hallo@kolmar-beispiel.de
      </li>
      <li>
        <svg class="contact-icon" viewBox="0 0 24 24" aria-hidden="true"><circle cx="12" cy="12" r="10" fill="var(--gold)"/><g fill="none" stroke="#fff" stroke-width="1.4"><ellipse cx="12" cy="12" rx="4" ry="10"/><path d="M2 12h20M4 7h16M4 17h16"/></g></svg>
        www.bettina-kolmar-beispiel.de
      </li>
    </ul>
  </section>

  <section class="card card-back" aria-label="Rückseite">
    <div class="back-pattern" role="img" aria-label="Zartes Blattmuster in Beige und Salbeigrün"></div>
    <div class="back-brand">
      <div class="brand-name">Bettina Kolmar</div>
      <div class="brand-tagline">Natur, Pflege &amp; Stil</div>
    </div>
  </section>

</body>
</html>
```